Payday Lending App Interface Design

Hello, we are building a payday lending application, Lendoro, that lend people money. I have drafted some of the screens that show the functionalities we have at the moment, please find the screens in attachments.
The elements in the screens are placed just to show what should be included in those screens, it's not necessary to follow the same layout. If you have better design ideas, you are very welcomed to show off your talent.
I think what we want is a style guide so that we can apply the same style to any screens that are similar to the ones I attached. We really like
the style as in the attached image called Style.png. We might want something similar - a simple, clean design yet fun and engaging. Customised graphical elements such as icons, illustrations are preferable.
Apart from the attached screens, we might also need a design for the On Board screen and the Login/Sign Up screen too.
Our logo colour is in yellow and black. Perhaps we will have a similar colour theme. I also attached the logo file, icon-Lendoro.png, if you would like to put it in your design.
Please message me if you need further information.
Regards
Target Market(s)
Young people that doesn't have strong income

```html
<!DOCTYPE html>
<html lang="en">
<head>
<meta charset="utf-8">
<title>Lendoro – App Screens</title>
<link rel="stylesheet" href="https://fonts.googleapis.com/css2?family=Poppins:wght@400;600;700&display=swap">
<style>
  :root{
    --canvas:#ffffff;
    --yellow:#f7d316;
    --yellow-deep:#e9c40f;
    --yellow-bar:#e2c21f;
    --ink:#0b0b0b;
    --field:#ffffff;
    --field-text:#333333;
  }
  *{box-sizing:border-box;margin:0;padding:0}
  html,body{width:1200px;height:588px;overflow:hidden;background:var(--canvas)}
  body{position:relative;font-family:"Poppins",sans-serif;color:var(--ink)}

  .screen{position:absolute;top:62px;width:223px;height:482px;overflow:hidden;background:var(--yellow)}
  .screen--details{left:58px}
  .screen--connecting{left:360px;top:49px;width:227px;height:499px;border-radius:22px}
  .screen--settings{left:647px}
  .screen--bank{left:912px}

  .backdrop{position:absolute;inset:0;background:linear-gradient(180deg,#f9d81a 0%,#eecb12 55%,#f4d114 100%)}
  .backdrop--fabric{background:linear-gradient(160deg,#f3cf12 0%,#f9da2a 40%,#ebc60f 100%)}

  .topbar{position:absolute;left:0;top:0;width:100%;height:38px;background:var(--yellow-bar);border-radius:0 0 10px 10px;box-shadow:0 3px 6px rgba(0,0,0,.08)}
  .topbar svg{position:absolute;top:12px}
  .topbar .icon-back{left:8px}
  .topbar .icon-close{right:10px}

  .brand-tile{position:absolute;left:50%;transform:translateX(-50%);background:var(--yellow);border-radius:12px;display:flex;align-items:center;justify-content:center;font-weight:700;color:var(--ink)}
  .brand-tile--small{top:84px;width:76px;height:44px;font-size:15px}
  .screen--bank .brand-tile--small{top:68px}
  .brand-tile--large{top:84px;width:143px;height:145px;border-radius:22px;font-size:30px}

  .title{position:absolute;left:12px;font-weight:600;font-size:16px;letter-spacing:.2px;line-height:1}
  .subtitle{position:absolute;left:12px;font-size:10px;line-height:1}

  .field{position:absolute;left:11px;width:202px;height:30px;background:var(--field);border-radius:2px;font-size:8.5px;color:var(--field-text);padding-left:14px;display:flex;align-items:center;box-shadow:0 1px 2px rgba(0,0,0,.06)}

  .btn{position:absolute;left:11px;width:202px;height:36px;background:var(--ink);color:#fff;border-radius:2px;font-weight:600;font-size:11px;display:flex;align-items:center;justify-content:center;letter-spacing:.2px}

  .status{position:absolute;top:8px;left:14px;font-size:7px;font-weight:600}
  .home-bar{position:absolute;bottom:4px;left:50%;transform:translateX(-50%);width:112px;height:3px;border-radius:2px;background:var(--ink)}

  .connecting-title{position:absolute;left:0;width:100%;top:265px;text-align:center;font-weight:600;font-size:22px;line-height:26px}
  .connecting-copy{position:absolute;left:0;width:100%;top:334px;text-align:center;font-size:12px;line-height:25px}

  .settings-title{position:absolute;left:13px;top:60px;font-weight:700;font-size:20px}

  .bank-name{position:absolute;left:13px;top:189px;display:flex;align-items:center;gap:6px;font-weight:700;font-size:14px}
  .bank-name .mark{width:14px;height:14px;background:var(--ink)}
</style>
</head>
<body>

  <!-- Personal details -->
  <section class="screen screen--details">
    <div class="backdrop" role="img" aria-label="Yellow-tinted photo of a modern office building"></div>
    <div class="topbar">
      <svg class="icon-back" width="22" height="14" viewBox="0 0 22 14"><path d="M20 7H3M8 2L2.5 7 8 12" fill="none" stroke="#0b0b0b" stroke-width="1.6" stroke-linecap="round"/></svg>
    </div>
    <div class="brand-tile brand-tile--small" style="top:84px">Lendoro</div>
    <h1 class="title" style="top:148px">PERSONAL DETAILS</h1>
    <p class="subtitle" style="top:171px">Please provide details as shown on ID</p>
    <div class="field" style="top:201px">Given Name</div>
    <div class="field" style="top:251px">Middle Name</div>
    <div class="field" style="top:301px">Surname</div>
    <div class="field" style="top:351px">Date of Birth (dd/mm/yr)</div>
    <div class="btn" style="top:435px">NEXT</div>
  </section>

  <!-- Connecting -->
  <section class="screen screen--connecting">
    <div class="backdrop" role="img" aria-label="Yellow-tinted photo of a glass skyscraper"></div>
    <div class="topbar" style="height:39px"></div>
    <span class="status">9:41</span>
    <div class="brand-tile brand-tile--large">Lendoro</div>
    <h1 class="connecting-title">CONNECTING TO<br>YOU BANK...</h1>
    <p class="connecting-copy">Please don't exit the app.<br>it takes 3-5 minutes to confirm<br>your details with your bank</p>
    <div class="home-bar"></div>
  </section>

  <!-- Settings -->
  <section class="screen screen--settings">
    <div class="backdrop backdrop--fabric" role="img" aria-label="Yellow-tinted photo of a woven architectural facade"></div>
    <div class="topbar">
      <svg class="icon-close" width="14" height="14" viewBox="0 0 14 14"><path d="M1 1l12 12M13 1L1 13" stroke="#0b0b0b" stroke-width="1.4" stroke-linecap="round"/></svg>
    </div>
    <h1 class="settings-title">SETTINGS</h1>
    <div class="btn" style="top:186px">PERSONAL DETAILS</div>
    <div class="btn" style="top:253px">BANK ACCOUNTS</div>
    <div class="btn" style="top:320px">ACCOUNTS SETTINGS</div>
    <div class="home-bar"></div>
  </section>

  <!-- Connect your bank -->
  <section class="screen screen--bank">
    <div class="backdrop" role="img" aria-label="Yellow-tinted photo of a modern office building"></div>
    <div class="topbar">
      <svg class="icon-back" width="22" height="14" viewBox="0 0 22 14"><path d="M20 7H3M8 2L2.5 7 8 12" fill="none" stroke="#0b0b0b" stroke-width="1.6" stroke-linecap="round"/></svg>
    </div>
    <div class="brand-tile brand-tile--small">Lendoro</div>
    <h1 class="title" style="top:136px">CONNECT YOUR BANK</h1>
    <div class="bank-name"><span class="mark"></span>Northvale</div>
    <div class="field" style="top:225px">Account Number</div>
    <div class="field" style="top:275px">Password</div>
    <div class="btn" style="top:435px">CONNECT</div>
  </section>

</body>
</html>
```